Business Card Design

Business Card for professional consulting firm working with large financial institutions.

Target Market(s)

Executive buyers

Industry/Entity Type

Banking

Contact Information for Business Card

Mild creativity wanted. Not boring, but do elaborate artwork.

Font styles to use
Serif
Sans Serif

Colors

Designer to choose colors to be used in the design.

Requirements
Must have
• Standard business card features - company name, individual name, telephone, website, email, locations.
Nice to have
• Two colors
Should not have
• too many colors, fancy printing, cartoons.

```html
<!DOCTYPE html>
<html lang="en">
<head>
<meta charset="UTF-8">
<title>Vantora Advisory – Business Card</title>
<link rel="stylesheet" href="https://fonts.googleapis.com/css2?family=Roboto:wght@300;400&family=Roboto+Condensed:wght@500&display=swap">
<style>
  :root {
    --backdrop: #e6e1da;
    --card-front: #f4f4f4;
    --card-back: #c2c2c2;
    --ink: #111111;
    --ink-soft: #4a4a4a;
    --ink-muted: #a9a9a9;
    --band: #000000;
    --white: #ffffff;
    --brand-grey: #2a2a2a;
  }
  * { margin: 0; padding: 0; box-sizing: border-box; }
  html, body {
    width: 1200px; height: 960px; overflow: hidden;
    background: var(--backdrop);
    font-family: "Roboto", Arial, sans-serif;
  }
  .card {
    position: absolute;
    width: 600px; height: 343px;
    box-shadow: 0 2px 6px rgba(0,0,0,0.35);
  }
  .card--front { left: 314px; top: 113px; background: var(--card-front); }
  .card--back { left: 312px; top: 472px; background: var(--card-back); }

  .holder { position: absolute; left: 38px; top: 54px; }
  .holder__name {
    font-family: "Roboto Condensed", Arial, sans-serif;
    font-weight: 500; font-size: 23px; color: var(--ink); letter-spacing: 0.2px;
    line-height: 1;
  }
  .holder__title {
    font-family: "Roboto Condensed", Arial, sans-serif;
    font-weight: 500; font-size: 15px; color: var(--ink-muted);
    margin-top: 4px; line-height: 1;
  }
  .divider {
    position: absolute; left: 36px; width: 168px;
    border-top: 1.5px dotted var(--ink-soft);
  }
  .divider--top { top: 116px; }
  .divider--bottom { top: 205px; }

  .address {
    position: absolute; left: 38px; top: 139px;
    font-size: 14.5px; line-height: 18px; color: var(--ink-soft); font-style: normal;
  }
  .contacts {
    position: absolute; left: 38px; top: 230px; list-style: none;
    font-size: 14.5px; line-height: 19px; color: var(--ink-soft);
  }
  .contacts li { display: flex; align-items: center; gap: 7px; }
  .contacts svg { width: 14px; height: 14px; fill: var(--ink); flex: none; }

  .brand {
    position: absolute; display: flex; align-items: center; gap: 10px;
    font-family: "Roboto", Arial, sans-serif; font-weight: 300; white-space: nowrap;
  }
  .brand__dot { border-radius: 50%; flex: none; }
  .card--front .brand { left: 290px; top: 148px; font-size: 32px; color: var(--brand-grey); }
  .card--front .brand__dot { width: 14px; height: 14px; background: var(--brand-grey); }
  .card--back .brand { left: 0; right: 0; top: 144px; justify-content: center; font-size: 34px; color: var(--white); }
  .card--back .brand__dot { width: 14px; height: 14px; background: var(--white); }

  .web-band {
    position: absolute; left: 0; right: 0; top: 275px; height: 29px;
    background: var(--band); color: var(--white);
    display: flex; align-items: center; justify-content: center;
    font-size: 14px; letter-spacing: 5.2px;
  }
</style>
</head>
<body>
  <section class="card card--front">
    <div class="holder">
      <p class="holder__name">DANIEL REYES</p>
      <p class="holder__title">CEO/FOUNDER</p>
    </div>
    <div class="divider divider--top"></div>
    <address class="address">
      Vantora Advisory<br>
      4120 Harbor View Road<br>
      Juneau, Alaska 99801
    </address>
    <div class="divider divider--bottom"></div>
    <ul class="contacts">
      <li>
        <svg viewBox="0 0 16 16" aria-hidden="true"><path d="M3.6 1.2l2.3 2.5-1.2 1.8c.9 2 2.4 3.6 4.5 4.6l1.6-1.3 2.6 2.2-1.4 2.6C7 13.6 2.3 9 1.8 3.1z"/></svg>
        555 214 7789
      </li>
      <li>
        <svg viewBox="0 0 16 16" aria-hidden="true"><path d="M1 3.5h14v9H1z M1.8 4.2L8 9l6.2-4.8" fill="none" stroke="#111" stroke-width="0"/><path d="M1 3.5h14L8 8.6z"/><path d="M1 4.8l7 5.2 7-5.2v7.7H1z"/></svg>
        info@vantoraadvisory.com
      </li>
      <li>
        <svg viewBox="0 0 16 16" aria-hidden="true"><circle cx="8" cy="8" r="6.8" fill="none" stroke="#111" stroke-width="1.6"/><path d="M4 4.5c1.5.3 2.5 1.2 2 2.6-.5 1-1.8.8-1.8 2.3 0 1 .9 1.6.6 3.3A6 6 0 0 1 2 8c0-1.4.7-2.7 2-3.5zM9.5 2.5c1 .6 1 1.7 2 2 1 .3 2 1 2 2.3-.9.2-2 .1-2.6 1-.6 1 .3 2-.6 3.1-.7.8-1.8.5-2-.5-.3-1.3-1.6-1.4-1.2-2.8.4-1.2 2-1 2-2.4 0-1-.8-1.5.4-2.7z"/></svg>
        www.vantoraadvisory.com
      </li>
    </ul>
    <div class="brand"><span class="brand__dot"></span>Vantora Advisory</div>
  </section>

  <section class="card card--back">
    <div class="brand"><span class="brand__dot"></span>Vantora Advisory</div>
    <div class="web-band">www.vantoraadvisory.com</div>
  </section>
</body>
</html>
```